Breakfast Cafe - The Sunny Nook

It is for my breakfast and lunch cafe with a hawaiian / beach theme. I am open 7 days a week from 7am to 2pm. We serve traditional American food such as omelettes, pancakes, burgers and sandwiches. I'll upload my old card and my new logo to be used. We have a lot of day to day regulars who eat there during the week, our t-shirts actually say 'Locals Only' on them. Hope this helps. Thanks.

Target Market(s)

anyone who has an appetite!

Industry/Entity Type

American Restaurant

Contact Information for Business Card

4815C Marlow Grove Avenue
Long Beach, California
(555) 731-2294

Requirements
Must have
• Address and phone number easily readable.
Nice to have
• beach or tropical theme

```html
<!DOCTYPE html>
<html lang="en">
<head>
<meta charset="utf-8">
<title>The Sunny Nook – Business Card</title>
<link rel="stylesheet" href="https://fonts.googleapis.com/css2?family=Roboto:ital,wght@0,400;0,500;0,700;1,400&display=swap">
<style>
  :root {
    --page-bg: #efe9e1;
    --kraft-light: #d9b58a;
    --kraft-dark: #b08656;
    --cream-light: #f6efe6;
    --cream-dark: #eadccb;
    --ink: #141414;
    --band: #050505;
    --band-text: #e8bf86;
    --name-blue: #3fa9c9;
    --sub-brown: #8a4f1f;
    --badge-orange: #f0a545;
    --badge-ring: #9b5a22;
  }
  * { box-sizing: border-box; margin: 0; padding: 0; }
  html, body { width: 1200px; height: 900px; overflow: hidden; }
  body {
    background: var(--page-bg);
    font-family: "Roboto", Arial, sans-serif;
    position: relative;
  }
  .card {
    position: absolute;
    left: 330px;
    width: 556px;
    height: 345px;
    overflow: hidden;
  }
  .card-front {
    top: 90px;
    background: linear-gradient(160deg, var(--kraft-light) 0%, var(--kraft-dark) 100%);
    color: var(--ink);
    text-align: center;
  }
  .card-back {
    top: 469px;
    background: linear-gradient(160deg, var(--cream-light) 0%, var(--cream-dark) 100%);
    text-align: center;
  }
  .brand-name {
    position: absolute;
    left: 0; right: 0;
    font-weight: 700;
    font-size: 36px;
    line-height: 1;
    z-index: 1;
  }
  .card-front .brand-name { top: 54px; color: var(--ink); }
  .brand-city {
    position: absolute;
    left: 0; right: 0;
    font-weight: 700;
    font-size: 11px;
    letter-spacing: 2.5px;
    z-index: 1;
  }
  .card-front .brand-city { top: 100px; color: var(--ink); }
  .address {
    position: absolute;
    top: 130px; left: 0; right: 0;
    font-size: 16px;
    line-height: 21px;
  }
  .phone {
    position: absolute;
    top: 178px; left: 0; right: 0;
    font-size: 22px;
  }
  .phone-label { font-weight: 500; }
  .tagline {
    position: absolute;
    top: 231px; left: 0; right: 0;
    font-size: 20px;
    font-style: italic;
  }
  .band {
    position: absolute;
    left: 0; right: 0;
    height: 53px;
    background: var(--band);
    color: var(--band-text);
    font-size: 20px;
    line-height: 53px;
  }
  .card-front .band { top: 271px; }
  .card-back .band { top: 270px; height: 50px; line-height: 50px; font-size: 19px; }
  .badge {
    position: absolute;
    top: 44px; left: 205px;
    width: 146px; height: 146px;
  }
  .card-back .brand-name { top: 198px; color: var(--name-blue); font-size: 32px; }
  .card-back .brand-city { top: 237px; color: var(--sub-brown); }
</style>
</head>
<body>
  <section class="card card-front">
    <h1 class="brand-name">The Sunny Nook</h1>
    <p class="brand-city">LONG BEACH, CA</p>
    <p class="address">4815C Marlow Grove Avenue<br>Long Beach, California</p>
    <p class="phone"><span class="phone-label">Phone:</span> (555) 731-2294</p>
    <p class="tagline">Family owned and operated!</p>
    <p class="band">Breakfast &amp; Lunch 7am - 2pm Daily</p>
  </section>

  <section class="card card-back">
    <svg class="badge" viewBox="0 0 146 146" role="img" aria-label="Round beach scene emblem with palm tree, sunset and ocean">
      <circle cx="73" cy="73" r="68" fill="var(--badge-orange)" stroke="var(--badge-ring)" stroke-width="9"/>
    </svg>
    <h2 class="brand-name">The Sunny Nook</h2>
    <p class="brand-city">LONG BEACH, CA</p>
    <p class="band">Omelettes | Pancakes | Burgers | Sandwiches</p>
  </section>
</body>
</html>
```